Duct Manufacturing Company new to the industry needs business card and stationary design

we are sheet metal duct manufacturers looking for a business card design to fit my new business logo.
nothing to crazy that will date, but want it to stand out from the crowed.
I'm sure you guys will work it out.

Contact Information for Business Card

Glen Marsh
Director

Address
17 Dorwell St
Larkfield NSW 2790

0438 760 514

Sales@flowbend.com.au

Font styles to use
Other font styles liked:
• BankGothic md bt

Requirements
Nice to have
• Like the idea of corner rounded to match logo
• like to keep colours flowing
• font I like sharp square not rounded

```html
<!DOCTYPE html>
<html lang="en">
<head>
<meta charset="utf-8">
<title>Flowbend Industries – Business Card</title>
<link rel="stylesheet" href="https://fonts.googleapis.com/css2?family=Michroma&family=Roboto+Condensed:wght@400&display=swap">
<style>
  :root {
    --backdrop: #9c9b9c;
    --card: #fbfbfb;
    --green: #7cc242;
    --green-deep: #3aa84a;
    --blue: #1a62ad;
    --blue-deep: #1b4595;
    --navy-text: #1d4f9c;
    --grey-text: #555a5f;
    --white: #ffffff;
  }
  * { box-sizing: border-box; margin: 0; padding: 0; }
  html, body { width: 1200px; height: 1200px; overflow: hidden; }
  body { background: var(--backdrop); position: relative; font-family: "Roboto Condensed", sans-serif; }

  .card {
    position: absolute;
    width: 712px;
    height: 418px;
    background: var(--card);
    border-radius: 24px;
    overflow: hidden;
  }
  .card--front { left: 238px; top: 118px; }
  .card--back  { left: 230px; top: 644px; }

  .front-band {
    position: absolute;
    left: 0; bottom: 0;
    width: 100%; height: 16px;
    background: linear-gradient(90deg, var(--green-deep), var(--green) 55%, var(--blue) 80%, var(--blue-deep));
  }

  .brand {
    position: absolute;
    display: flex;
    align-items: center;
    gap: 14px;
  }
  .brand__dot {
    width: 26px; height: 26px;
    border-radius: 50%;
    background: var(--green);
    flex: none;
  }
  .brand__name {
    font-family: "Michroma", sans-serif;
    color: var(--blue-deep);
    font-size: 34px;
    line-height: 1.25;
    letter-spacing: 1px;
  }
  .card--front .brand { left: 50%; top: 190px; transform: translateX(-50%); }
  .card--back .brand { left: 58px; top: 150px; }
  .card--back .brand__name { font-size: 30px; }

  .holder {
    position: absolute;
    right: 37px;
    top: 68px;
    text-align: right;
  }
  .holder__name {
    font-family: "Michroma", sans-serif;
    color: var(--navy-text);
    font-size: 22px;
    letter-spacing: 2px;
  }
  .holder__role {
    font-family: "Michroma", sans-serif;
    color: var(--grey-text);
    font-size: 14px;
    margin-top: 6px;
    letter-spacing: 0.5px;
  }

  .back-panel {
    position: absolute;
    left: 0; bottom: 0;
    width: 100%; height: 152px;
    background: linear-gradient(100deg, var(--green) 0%, var(--blue) 38%, var(--blue-deep) 100%);
  }

  .contact {
    position: absolute;
    right: 36px;
    top: 282px;
    list-style: none;
    color: var(--white);
    font-size: 18px;
    text-align: right;
  }
  .contact__item {
    display: flex;
    justify-content: flex-end;
    align-items: center;
    gap: 14px;
    height: 26.5px;
  }
  .contact__item--address { margin-top: 3px; }
  .contact__icon { width: 18px; height: 18px; flex: none; }
</style>
</head>
<body>

  <section class="card card--front">
    <div class="brand">
      <span class="brand__dot"></span>
      <span class="brand__name">FLOWBEND<br>INDUSTRIES</span>
    </div>
    <div class="front-band" role="img" aria-label="Decorative green to blue band along the bottom edge"></div>
  </section>

  <section class="card card--back">
    <div class="back-panel" role="img" aria-label="Decorative green and blue flowing wave artwork"></div>

    <div class="brand">
      <span class="brand__dot"></span>
      <span class="brand__name">FLOWBEND<br>INDUSTRIES</span>
    </div>

    <div class="holder">
      <p class="holder__name">GLEN MARSH</p>
      <p class="holder__role">Director</p>
    </div>

    <ul class="contact">
      <li class="contact__item">0438 760 514
        <svg class="contact__icon" viewBox="0 0 18 18" aria-hidden="true"><path d="M2,6 C2,3 5,2 9,2 C13,2 16,3 16,6 L13,7 L12,5 L6,5 L5,7 Z M4,9 L14,9 L15,16 L3,16 Z" fill="#fff"/></svg>
      </li>
      <li class="contact__item">flowbend.com.au
        <svg class="contact__icon" viewBox="0 0 18 18" aria-hidden="true"><g fill="none" stroke="#fff" stroke-width="1.5"><circle cx="9" cy="9" r="7"/><ellipse cx="9" cy="9" rx="3" ry="7"/><line x1="2" y1="9" x2="16" y2="9"/></g></svg>
      </li>
      <li class="contact__item">sales@flowbend.com.au
        <svg class="contact__icon" viewBox="0 0 18 18" aria-hidden="true"><rect x="1" y="4" width="16" height="11" fill="#fff"/><path d="M1,4 L9,10 L17,4" fill="none" stroke="#1b4595" stroke-width="1.3"/></svg>
      </li>
      <li class="contact__item contact__item--address">17 Dorwell St Larkfield NSW 2790</li>
    </ul>
  </section>

</body>
</html>
```